Corporate Dinner Invite at Corvessa for BRQ

BRQ is hosting a corporate dinner at the VEP Summit and we need an email attachment invite for the event. Please use some images from this site for inspiration: https://www.corvessadining.example/ivyparlor/

Invite Title:
Join us for dinner!

Event Details:
Tuesday, October 24th 2023 at 6:30pm
Corvessa Dining, Ivy Parlor
347 W Marlow Ave, Chicago, IL 60622

Target Market(s)

Corporate Audience

Font styles to use
Script

Colors
0054AA
0677BA
7BADD7
CADEEF
E8F1F8

Requirements
Must have
• BRQ logo, event date / time, event location details, photo(s) from Ivy Parlor

```html
<!DOCTYPE html>
<html lang="en">
<head>
<meta charset="utf-8">
<title>BRQ Dinner Invitation – Ivy Parlor</title>
<link href="https://fonts.googleapis.com/css2?family=Allura&family=Crimson+Text:wght@400;600&display=swap" rel="stylesheet">
<style>
  :root {
    --ink: #ffffff;
    --room-dark: #1c120d;
    --room-mid: #3d2a1f;
    --room-warm: #6a4a33;
    --wall: #4a3a2c;
    --glow: #d9b07a;
    --amber: #c98a45;
    --divider: #e9c9a6;
    --bar-dark: #140d09;
    --bar-warm: #5b3a22;
    --marble: #e8e2da;
  }
  html, body {
    margin: 0;
    padding: 0;
    width: 848px;
    height: 1200px;
    overflow: hidden;
    background: var(--room-dark);
  }
  .invite {
    position: relative;
    width: 848px;
    height: 1200px;
    overflow: hidden;
    background: var(--divider);
    font-family: "Crimson Text", Georgia, serif;
    color: var(--ink);
  }
  .hero-photo {
    position: absolute;
    left: 0; top: 0;
    width: 848px; height: 980px;
    background:
      radial-gradient(ellipse 200px 170px at 50% 22%, rgba(217,176,122,0.55), transparent 75%),
      radial-gradient(ellipse 150px 110px at 47% 44%, rgba(179,138,92,0.35), transparent 75%),
      radial-gradient(ellipse 60px 60px at 15% 46%, rgba(217,176,122,0.25), transparent 80%),
      radial-gradient(ellipse 60px 60px at 85% 46%, rgba(217,176,122,0.2), transparent 80%),
      linear-gradient(90deg, rgba(20,13,9,0.55) 0%, transparent 14%, transparent 86%, rgba(20,13,9,0.55) 100%),
      linear-gradient(180deg, #2e2018 0%, var(--room-warm) 20%, var(--wall) 45%, var(--room-mid) 62%, #2a1c14 74%, #3a2a1e 84%, var(--room-dark) 100%);
  }
  .brand {
    position: absolute;
    top: 100px; left: 0; width: 848px;
    display: flex;
    justify-content: center;
    align-items: center;
    gap: 16px;
  }
  .brand-square {
    width: 34px; height: 34px;
    background: var(--ink);
  }
  .brand-name {
    font-size: 80px;
    font-weight: 600;
    letter-spacing: 4px;
    line-height: 1;
  }
  .title-script {
    position: absolute;
    left: 0; width: 848px;
    text-align: center;
    font-family: "Allura", cursive;
    line-height: 1;
    margin: 0;
    font-weight: 400;
  }
  .title-join { top: 212px; font-size: 300px; letter-spacing: 0; }
  .title-for {
    position: absolute;
    top: 476px; left: 0; width: 848px;
    text-align: center;
    font-size: 66px;
    letter-spacing: 18px;
    line-height: 1;
    padding-left: 40px;
    box-sizing: border-box;
  }
  .title-dinner { top: 462px; font-size: 262px; padding-left: 50px; box-sizing: border-box; }
  .details {
    position: absolute;
    top: 784px; left: 0; width: 848px;
    text-align: center;
    font-size: 43px;
    line-height: 52px;
    letter-spacing: 1.2px;
  }
  .details p { margin: 0; }
  .gallery-photo {
    position: absolute;
    top: 984px;
    height: 216px;
  }
  .gallery-bartender {
    left: 0; width: 352px;
    background:
      radial-gradient(ellipse 40px 40px at 62% 80%, rgba(255,190,110,0.7), transparent 80%),
      radial-gradient(ellipse 50px 60px at 38% 70%, rgba(230,160,80,0.55), transparent 80%),
      radial-gradient(ellipse 25px 25px at 18% 92%, rgba(255,190,110,0.5), transparent 80%),
      radial-gradient(ellipse 25px 25px at 90% 88%, rgba(255,190,110,0.45), transparent 80%),
      linear-gradient(180deg, #2a1d15 0%, var(--bar-dark) 55%, #3a2a1e 88%, #8a7563 100%);
  }
  .gallery-cocktails {
    left: 357px; width: 491px;
    background:
      radial-gradient(ellipse 120px 80px at 30% 55%, rgba(240,180,100,0.45), transparent 80%),
      radial-gradient(ellipse 120px 80px at 75% 55%, rgba(240,180,100,0.4), transparent 80%),
      linear-gradient(180deg, var(--bar-dark) 0%, #4a2e1a 28%, var(--bar-warm) 50%, var(--amber) 72%, #b59a80 86%, var(--marble) 100%);
  }
</style>
</head>
<body>
  <main class="invite">
    <div class="hero-photo" role="img" aria-label="Ivy Parlor dining room with ornate chandelier, textured walls and velvet banquettes"></div>

    <div class="brand">
      <span class="brand-square"></span>
      <span class="brand-name">BRQ</span>
    </div>

    <h1 class="title-script title-join">Join Us</h1>
    <div class="title-for">FOR</div>
    <div class="title-script title-dinner">Dinner!</div>

    <section class="details">
      <p>Tuesday, October 24th 2023 at 6:30pm</p>
      <p>Corvessa Dining, Ivy Parlor</p>
      <p>347 W Marlow Ave, Chicago, IL 60622</p>
    </section>

    <div class="gallery-photo gallery-bartender" role="img" aria-label="Bartender straining a cocktail beside a candle and menu"></div>
    <div class="gallery-photo gallery-cocktails" role="img" aria-label="Row of signature cocktails on a marble bar"></div>
  </main>
</body>
</html>
```